Rebrand stationary with recently completed logo design

Need new business cards, thank you cards, letterhead, envelopes and presentation folders. The designs will be sent to a separate production firm so I need the files to be print ready.

My contact info
Reko Haliburn

Office 604-318-5047
Fax 604-371-8054

Email reko@glazemark.ca
website www.glazemark.ca

315-14720 62nd Avenue,
Langley, BC, V2K 3R8

Target Market(s)

Homeowners, businesses and contractors

Industry/Entity Type

Business

Font styles to use
Sans Serif

Colors
34a7d7

Requirements
Must have
• Like to have one side of the business card a solid color with the logo in all white. The side with all the text to be a white background
• I find the current blue on the front of the card with the white logo too dark.
Should not have
• Gradient colors

```html
<!DOCTYPE html>
<html lang="en">
<head>
<meta charset="utf-8">
<title>Glazemark business card</title>
<link rel="stylesheet" href="https://fonts.googleapis.com/css2?family=Open+Sans:wght@400;600&family=PT+Sans+Narrow:wght@700&display=swap">
<style>
  :root {
    --backdrop: #e6e3df;
    --card-white: #f7f7f7;
    --slate: #3e4c56;
    --blue: #1b8fd4;
    --text-dark: #4a4f53;
    --tagline-grey: #8a949a;
    --tagline-back: #7b8a93;
    --white: #ffffff;
  }
  * { margin: 0; padding: 0; box-sizing: border-box; }
  html, body { width: 1200px; height: 960px; overflow: hidden; }
  body {
    position: relative;
    background: var(--backdrop);
    font-family: "Open Sans", Arial, sans-serif;
  }
  .card {
    position: absolute;
    width: 600px;
    height: 342px;
    box-shadow: 0 3px 8px rgba(0,0,0,0.25);
  }
  .card--front { left: 302px; top: 129px; background: var(--card-white); }
  .card--back { left: 299px; top: 488px; background: var(--slate); }

  .brand { position: absolute; }
  .brand__mark { position: absolute; background: var(--slate); }
  .brand__name {
    position: absolute;
    white-space: nowrap;
    font-weight: 400;
    letter-spacing: 0.5px;
    line-height: 1;
  }
  .brand__tagline {
    position: absolute;
    white-space: nowrap;
    text-transform: uppercase;
    letter-spacing: 1.4px;
    line-height: 1;
  }

  .card--front .brand__mark { left: 113px; top: 46px; width: 30px; height: 30px; }
  .card--front .brand__name { left: 36px; top: 117px; font-size: 29px; color: var(--blue); }
  .card--front .brand__tagline { left: 38px; top: 147px; font-size: 10.5px; color: var(--tagline-grey); }

  .address {
    position: absolute;
    left: 38px;
    top: 185px;
    font-size: 12.5px;
    line-height: 18px;
    color: var(--text-dark);
  }
  .contact-list {
    position: absolute;
    left: 38px;
    top: 228px;
    list-style: none;
    font-size: 12.5px;
    color: var(--text-dark);
  }
  .contact-list li { display: flex; align-items: center; height: 19px; }
  .contact-list svg { width: 14px; height: 14px; margin-right: 8px; fill: var(--blue); }

  .name-tab {
    position: absolute;
    left: 392px;
    top: 218px;
    width: 208px;
    height: 54px;
    background: var(--slate);
    border-left: 4px solid var(--blue);
    display: flex;
    align-items: center;
    padding-left: 22px;
    font-family: "PT Sans Narrow", "Arial Narrow", sans-serif;
    font-weight: 700;
    font-size: 20px;
    letter-spacing: 0.3px;
    color: var(--white);
    text-transform: uppercase;
  }

  .card--back .brand__mark { left: 131px; top: 130px; width: 56px; height: 56px; background: var(--white); }
  .card--back .brand__name { left: 202px; top: 138px; font-size: 44px; color: var(--white); }
  .card--back .brand__tagline { left: 204px; top: 184px; font-size: 16.5px; color: var(--tagline-back); letter-spacing: 1.8px; }
</style>
</head>
<body>
  <section class="card card--front" aria-label="Business card front">
    <div class="brand">
      <span class="brand__mark"></span>
      <span class="brand__name">GLAZEMARK</span>
      <span class="brand__tagline">Beyond glass coatings</span>
    </div>
    <p class="address">315-14720 62nd Avenue<br>Langley, BC, V2K 3R8</p>
    <ul class="contact-list">
      <li><svg viewBox="0 0 16 16" aria-hidden="true"><path d="M3.6 1.2l2.3 2.6-1.3 1.7c.9 2 2.4 3.5 4.4 4.4l1.7-1.3 2.6 2.3-1.4 2.3C7 13 3 9 1.2 3.1z"/></svg>604-318-5047</li>
      <li><svg viewBox="0 0 16 16" aria-hidden="true"><rect x="4" y="1" width="8" height="4"/><rect x="1" y="6" width="14" height="6" rx="1"/><rect x="4" y="10" width="8" height="5"/></svg>604-371-8054</li>
      <li><svg viewBox="0 0 16 16" aria-hidden="true"><path d="M1 4h14v9H1z M1 4l7 5 7-5" stroke="#f7f7f7" stroke-width="1"/></svg>reko@glazemark.ca</li>
      <li><svg viewBox="0 0 16 16" aria-hidden="true"><circle cx="8" cy="8" r="7"/><path d="M5 4c2 1 1 3 3 3s1 3 3 4M9 2c0 2 3 2 4 3" stroke="#f7f7f7" stroke-width="1.3" fill="none"/></svg>www.glazemark.ca</li>
    </ul>
    <div class="name-tab">Reko Haliburn</div>
  </section>

  <section class="card card--back" aria-label="Business card back">
    <div class="brand">
      <span class="brand__mark"></span>
      <span class="brand__name">GLAZEMARK</span>
      <span class="brand__tagline">Beyond glass coatings</span>
    </div>
  </section>
</body>
</html>
```